Presentation Folder with inside Pockets

We need a Presentation Folder with inside pockets. The size of the folder will be 9" x 12" and will be printed on the cover, the back and the inside folder flaps. The design will be very simple and consist of our logo (large) on the front cover and our logo (smaller) and contact information on the back. We are open to various colors that you think may go along with our logo. When you display your work, show the front, back and inside.

Target Market(s)

Pharmaceutical Companies

Industry/Entity Type

Work

Requirements
Should not have
• please do not add stock medical photos.

```html
<!DOCTYPE html>
<html lang="en">
<head>
<meta charset="utf-8">
<title>Corvane Systems Inc. – Presentation Folder</title>
<link rel="stylesheet" href="https://fonts.googleapis.com/css2?family=Open+Sans:wght@400;600;800&display=swap">
<style>
  :root{
    --backdrop:#000000;
    --paper:#f4f4f5;
    --ink:#141414;
    --navy:#123a66;
    --blue:#1b7cc0;
    --faint:#e4e7e2;
    --fold:#c9c9cc;
    --web:#e8eef4;
  }
  *{margin:0;padding:0;box-sizing:border-box}
  html,body{width:1200px;height:975px;overflow:hidden;background:var(--backdrop)}
  .folder{position:relative;width:1200px;height:975px;font-family:"Open Sans",Arial,sans-serif}
  .folder-art{position:absolute;left:0;top:0}
  .brand{position:absolute;display:flex;align-items:center;gap:14px;color:var(--ink);
    font-weight:800;text-transform:uppercase;white-space:nowrap;letter-spacing:.5px}
  .brand-dot{border-radius:50%;background:var(--blue);flex:none}
  .brand--back{left:92px;width:506px;top:255px;flex-direction:column;gap:26px;font-size:30px}
  .brand--back .brand-dot{width:110px;height:110px}
  .brand--front{left:630px;top:92px;font-size:25px}
  .brand--front .brand-dot{width:64px;height:64px}
  .contact{position:absolute;left:132px;top:629px;color:#fff;font-size:13px;line-height:26px}
  .contact-row{display:flex;align-items:center;gap:7px}
  .contact-row svg{flex:none}
  .web{position:absolute;right:130px;top:700px;font-size:13px;letter-spacing:2.4px;color:var(--web)}
  .card{position:absolute;top:780px;width:197px;height:113px;background:#fff;padding:10px 10px;
    color:var(--ink);font-size:5.5px;line-height:8px}
  .card--left{left:229px}
  .card--right{left:770px}
  .card .brand{position:static;font-size:8.5px;gap:5px;letter-spacing:.2px}
  .card .brand-dot{width:16px;height:16px}
  .card-contact{position:absolute;left:12px;top:64px}
  .card-person{position:absolute;right:18px;top:66px;text-align:center;font-weight:600;font-size:6px}
  .card-person span{display:block;font-weight:400}
</style>
</head>
<body>
<div class="folder">
  <svg class="folder-art" width="1200" height="975" viewBox="0 0 1200 975" aria-hidden="true">
    <defs>
      <linearGradient id="band" x1="0" y1="0" x2="1" y2="0">
        <stop offset="0" stop-color="#123a66"/>
        <stop offset=".5" stop-color="#1b82c6"/>
        <stop offset="1" stop-color="#134a7e"/>
      </linearGradient>
      <radialGradient id="pocketBlue" cx=".55" cy=".45" r=".7">
        <stop offset="0" stop-color="#1d8ad0"/>
        <stop offset="1" stop-color="#14497f"/>
      </radialGradient>
      <radialGradient id="pocketGreen" cx=".55" cy=".45" r=".7">
        <stop offset="0" stop-color="#a6cf45"/>
        <stop offset="1" stop-color="#5f9a33"/>
      </radialGradient>
    </defs>
    <!-- folder covers -->
    <rect class="cover" x="92" y="42" width="1014" height="676" fill="var(--paper)"/>
    <line x1="598" y1="42" x2="598" y2="718" stroke="var(--fold)" stroke-width="1"/>
    <!-- faint front decoration -->
    <circle cx="862" cy="442" r="188" fill="var(--faint)" opacity=".7"/>
    <!-- wave band -->
    <path d="M92,600 C150,586 260,580 400,604 C500,621 560,638 650,658 C800,690 980,682 1106,572 L1106,718 L92,718 Z" fill="url(#band)"/>
    <path d="M104,598 C170,584 270,582 400,603" fill="none" stroke="#ffffff" stroke-width="2" opacity=".8"/>
    <path d="M380,612 C520,640 600,664 720,682 C850,700 960,694 1040,668 C960,704 840,708 720,692 C600,676 500,646 380,612 Z" fill="#ffffff" opacity=".92"/>
    <!-- pockets -->
    <path d="M47,742 L92,730 L598,730 L590,945 L86,945 L47,905 Z" fill="url(#pocketBlue)"/>
    <path d="M598,730 L1106,730 L1150,742 L1150,905 L1112,945 L628,945 L610,930 Z" fill="url(#pocketGreen)"/>
    <!-- card slits -->
    <g stroke="#cfd6dc" stroke-width="1">
      <line x1="218" y1="772" x2="244" y2="796"/><line x1="437" y1="772" x2="411" y2="796"/>
      <line x1="218" y1="900" x2="244" y2="876"/><line x1="437" y1="900" x2="411" y2="876"/>
      <line x1="760" y1="772" x2="786" y2="796"/><line x1="979" y1="772" x2="953" y2="796"/>
      <line x1="760" y1="900" x2="786" y2="876"/><line x1="979" y1="900" x2="953" y2="876"/>
    </g>
  </svg>

  <div class="brand brand--back"><span class="brand-dot"></span>Corvane Systems Inc.</div>

  <div class="contact">
    <div class="contact-row">
      <svg width="13" height="13" viewBox="0 0 16 16"><path d="M4 1l3 4-2 2c1 2 2 3 4 4l2-2 4 3-2 3C7 15 1 9 1 3z" fill="#fff"/></svg>
      +1-555-014-2760
    </div>
    <div class="contact-row">
      <svg width="14" height="12" viewBox="0 0 16 13"><path d="M1 1h14v11H1z M1 1l7 6 7-6" fill="none" stroke="#fff" stroke-width="1.6"/></svg>
      hello@corvane.net
    </div>
    <div class="contact-row">Corvane Systems, Inc. 214 Elm Avenue, Fairview, NY 11802</div>
  </div>

  <div class="brand brand--front"><span class="brand-dot"></span>Corvane Systems Inc.</div>
  <div class="web">www.corvane.net</div>

  <div class="card card--left">
    <div class="brand"><span class="brand-dot"></span>Corvane Systems Inc.</div>
    <div class="card-contact">+1-555-014-2760<br>hello@corvane.net<br><br>Corvane Systems, Inc. 214 Elm Avenue<br>Fairview, NY 11802</div>
    <div class="card-person">Your Name<span>Title</span></div>
  </div>
  <div class="card card--right">
    <div class="brand"><span class="brand-dot"></span>Corvane Systems Inc.</div>
    <div class="card-contact">+1-555-014-2760<br>hello@corvane.net<br><br>Corvane Systems, Inc. 214 Elm Avenue<br>Fairview, NY 11802</div>
    <div class="card-person">Your Name<span>Title</span></div>
  </div>
</div>
</body>
</html>
```